professional business card design for technology company

We are a small technology consulting firm, specialising in consulting based around Cloud and Managed services. Our colour scheme is yellow, blue and white, as you can see in the logos. Although we are based in melbourne australia, due to the nature of our work, our clients can be located anywhere. We are looking for a clean, professional, positive look - similar to our company logo

Target Market(s)

small business

Industry/Entity Type

Business

Contact Information for Business Card

eye catching, designed to incorporate some level of raised printing. Must contain website address, phone number, name and job title

Requirements
Must have
• Logo (attached) - use of the same colour scheme

```html
<!DOCTYPE html>
<html lang="en">
<head>
<meta charset="utf-8">
<title>Nimbora Business Card</title>
<link href="https://fonts.googleapis.com/css2?family=Raleway:wght@400;500;600;800&display=swap" rel="stylesheet">
<style>
  :root {
    --blue: #2a97cb;
    --yellow: #f5d20a;
    --card: #f2f2f2;
    --ink: #4b4b4b;
    --line: #b9b9b9;
    --bg: #e4e2df;
  }
  * { box-sizing: border-box; margin: 0; padding: 0; }
  html, body { width: 1200px; height: 960px; overflow: hidden; }
  body {
    background: var(--bg);
    font-family: "Raleway", sans-serif;
    color: var(--ink);
    position: relative;
  }
  .card {
    position: absolute;
    left: 220px;
    width: 760px;
    height: 434px;
    background: var(--card);
    box-shadow: 0 6px 18px rgba(0,0,0,0.18);
    overflow: hidden;
  }
  .card--front { top: 20px; }
  .card--back { top: 506px; }
  .card-bands { position: absolute; inset: 0; width: 100%; height: 100%; }
  .brand {
    position: absolute;
    display: flex;
    align-items: center;
    gap: 16px;
  }
  .brand-dot {
    width: 34px; height: 34px;
    border-radius: 50%;
    background: var(--blue);
  }
  .brand-name {
    font-weight: 800;
    color: var(--ink);
    letter-spacing: -1px;
  }
  .card--front .brand { left: 50%; top: 50%; transform: translate(-50%, -50%); }
  .card--front .brand-name { font-size: 82px; }
  .card--back .brand { left: 60px; top: 96px; }
  .card--back .brand-name { font-size: 60px; }
  .card--back .brand-dot { width: 28px; height: 28px; }
  .divider {
    position: absolute;
    left: 420px; top: 68px;
    width: 1px; height: 268px;
    background: var(--line);
  }
  .person {
    position: absolute;
    left: 462px; top: 92px;
    display: flex; align-items: center; gap: 14px;
  }
  .icon-ring {
    width: 40px; height: 40px;
    border-radius: 50%;
    border: 2px solid var(--blue);
    display: flex; align-items: center; justify-content: center;
    flex-shrink: 0;
  }
  .icon-ring--small {
    width: 32px; height: 32px;
    border: 2px solid #666;
  }
  .person-name { font-size: 22px; font-weight: 800; color: var(--ink); line-height: 1; }
  .person-name .surname { font-weight: 500; color: var(--blue); }
  .person-title { font-size: 15px; font-weight: 500; color: #777; margin-top: 4px; }
  .contacts {
    position: absolute;
    left: 462px; top: 200px;
    list-style: none;
    display: flex; flex-direction: column; gap: 14px;
  }
  .contact { display: flex; align-items: center; gap: 14px; font-size: 16px; font-weight: 500; color: #333; }
</style>
</head>
<body>

<section class="card card--front" aria-label="Card front">
  <svg class="card-bands" viewBox="0 0 760 434" preserveAspectRatio="none" aria-hidden="true">
    <rect x="0" y="0" width="760" height="14" fill="var(--blue)"/>
    <polygon points="0,14 350,14 340,24 0,24" fill="var(--yellow)"/>
    <polygon points="410,400 760,400 760,410 400,410" fill="var(--yellow)"/>
    <rect x="0" y="410" width="760" height="24" fill="var(--blue)"/>
  </svg>
  <div class="brand">
    <span class="brand-dot"></span>
    <span class="brand-name">Nimbora</span>
  </div>
</section>

<section class="card card--back" aria-label="Card back">
  <svg class="card-bands" viewBox="0 0 760 434" preserveAspectRatio="none" aria-hidden="true">
    <rect x="0" y="0" width="760" height="14" fill="var(--blue)"/>
    <polygon points="0,14 320,14 310,24 0,24" fill="var(--yellow)"/>
    <polygon points="380,392 760,392 760,404 368,404" fill="var(--yellow)"/>
    <rect x="0" y="404" width="760" height="30" fill="var(--blue)"/>
  </svg>

  <div class="brand">
    <span class="brand-dot"></span>
    <span class="brand-name">Nimbora</span>
  </div>

  <div class="divider"></div>

  <div class="person">
    <span class="icon-ring">
      <svg width="20" height="20" viewBox="0 0 20 20" aria-hidden="true">
        <circle cx="10" cy="6" r="4" fill="#555"/>
        <path d="M2 18 Q2 11 10 11 Q18 11 18 18 Z" fill="#555"/>
      </svg>
    </span>
    <div>
      <p class="person-name">DANIEL <span class="surname">HAYES</span></p>
      <p class="person-title">Sales Director</p>
    </div>
  </div>

  <ul class="contacts">
    <li class="contact">
      <span class="icon-ring icon-ring--small">
        <svg width="14" height="14" viewBox="0 0 14 14" aria-hidden="true">
          <path d="M3 1 L5 1 L6 4 L4.5 5.2 Q5.8 8.2 8.8 9.5 L10 8 L13 9 L13 11 Q13 13 11 13 Q1 12 1 3 Q1 1 3 1 Z" fill="var(--blue)"/>
        </svg>
      </span>
      <span>555-018-2740</span>
    </li>
    <li class="contact">
      <span class="icon-ring icon-ring--small">
        <svg width="16" height="16" viewBox="0 0 16 16" aria-hidden="true">
          <circle cx="8" cy="8" r="7" fill="var(--blue)"/>
          <ellipse cx="8" cy="8" rx="3" ry="7" fill="none" stroke="#fff" stroke-width="1"/>
          <line x1="1" y1="8" x2="15" y2="8" stroke="#fff" stroke-width="1"/>
        </svg>
      </span>
      <span>www.nimbora.com</span>
    </li>
    <li class="contact">
      <span class="icon-ring icon-ring--small">
        <svg width="16" height="12" viewBox="0 0 16 12" aria-hidden="true">
          <rect x="0" y="0" width="16" height="12" rx="1.5" fill="var(--blue)"/>
          <polyline points="1,1 8,7 15,1" fill="none" stroke="#fff" stroke-width="1.4"/>
        </svg>
      </span>
      <span>hello@nimbora.com</span>
    </li>
  </ul>
</section>

</body>
</html>
```